20 years in Business Magazine Ad

We need a half page advertisement, celebrating 20 years in business in 2016. We are a globalized Flavor and Fragrance Ingredient company called Vintrel Corp. I've attached a file of our current logos. I like the idea of the Globe with pearls- but we definitely need an updated version of it. Plus room for the website address, phone number and email address.

Industry/Entity Type

Business

Requirements
Must have
• Wording saying that we are celebrating 20 years in business
Nice to have
• Something that says to the reader that we are a global company

```html
<!DOCTYPE html>
<html lang="en">
<head>
<meta charset="utf-8">
<title>Vintrel Corp. – 20 Years in Business</title>
<link rel="stylesheet" href="https://fonts.googleapis.com/css2?family=Poiret+One&family=Oswald:wght@600;700&family=Roboto+Condensed:wght@700&display=swap">
<style>
  :root {
    --indigo: #2b2787;
    --sky-top: #d9ecf8;
    --sky-mid: #bcdcf1;
    --sky-low: #a9d2ee;
    --ocean: #1f6fc0;
    --ocean-deep: #0f4c9c;
    --ocean-light: #8cc3ea;
    --gold: #c39a48;
    --gold-light: #e3c57f;
    --white: #ffffff;
  }
  * { margin: 0; padding: 0; box-sizing: border-box; }
  html, body {
    width: 1200px; height: 1186px; overflow: hidden;
    background: #e9eef2;
  }
  .ad-page {
    position: relative;
    width: 1200px; height: 1186px;
    background: linear-gradient(180deg, var(--sky-top) 0%, var(--sky-mid) 55%, var(--sky-low) 100%);
    overflow: hidden;
  }
  .brand {
    position: absolute; left: 70px; top: 70px;
    display: flex; align-items: center; gap: 22px;
  }
  .brand-dot {
    width: 44px; height: 44px; border-radius: 50%;
    background: var(--indigo);
  }
  .brand-name {
    font-family: "Poiret One", sans-serif;
    font-size: 118px; line-height: 1;
    color: var(--indigo);
  }
  .tagline {
    position: absolute; left: 70px; top: 250px;
    font-family: "Poiret One", sans-serif; font-weight: 400;
    font-size: 82px; line-height: 1.08;
    color: var(--indigo);
  }
  .tagline span { display: block; }
  .tagline .line-two { padding-left: 110px; }
  .anniversary-badge {
    position: absolute; right: 70px; top: 70px;
    width: 320px; height: 320px;
  }
  .anniversary-badge .wreath {
    position: absolute; inset: 0; border-radius: 50%;
    border: 26px solid var(--gold);
    box-shadow: inset 0 0 0 6px var(--gold-light);
  }
  .badge-text {
    position: absolute; inset: 0;
    display: flex; flex-direction: column; align-items: center; justify-content: center;
    font-family: "Oswald", sans-serif; font-weight: 700;
    color: var(--gold); text-transform: uppercase; text-align: center;
  }
  .badge-text .small { font-size: 22px; letter-spacing: 2px; line-height: 1.15; }
  .badge-text .years-number { font-size: 92px; line-height: 0.95; margin: 2px 0 4px; }
  .hero-visual {
    position: absolute; left: 70px; right: 70px; top: 480px; bottom: 150px;
    border-radius: 36px;
    background: radial-gradient(ellipse at 50% 50%, var(--ocean) 0%, var(--ocean-deep) 45%, var(--ocean-light) 100%);
  }
  .contact-band {
    position: absolute; left: 0; right: 0; bottom: 40px; height: 70px;
    background: var(--indigo);
    display: flex; align-items: center; justify-content: space-around;
    font-family: "Roboto Condensed", sans-serif; font-weight: 700;
    font-size: 30px; color: var(--white);
  }
  .contact-item { display: flex; align-items: center; gap: 12px; }
  .contact-item svg { width: 30px; height: 30px; }
</style>
</head>
<body>
<main class="ad-page">
  <header class="brand">
    <span class="brand-dot"></span>
    <span class="brand-name">Vintrel</span>
  </header>

  <h1 class="tagline">
    <span>Not Just Better,</span>
    <span class="line-two">Always Better !</span>
  </h1>

  <div class="anniversary-badge">
    <div class="wreath" role="img" aria-label="Gold laurel wreath framing the anniversary badge"></div>
    <div class="badge-text">
      <span class="small">Celebrating</span>
      <span class="years-number">20</span>
      <span class="small">Years</span>
      <span class="small">in Business</span>
    </div>
  </div>

  <div class="hero-visual" role="img" aria-label="Photograph of a blue open seashell holding the Earth in place of a pearl"></div>

  <footer class="contact-band">
    <span class="contact-item">
      <svg viewBox="0 0 24 24" aria-hidden="true"><circle cx="12" cy="12" r="11" fill="#fff"/><path d="M8.5 6.5l2 .2.8 2.6-1.3 1.1a8 8 0 0 0 3.6 3.6l1.1-1.3 2.6.8.2 2-1.6 1.3c-4.5-.4-8.4-4.3-8.8-8.8z" fill="#2b2787"/></svg>
      (555) 014-2790
    </span>
    <span class="contact-item">
      <svg viewBox="0 0 24 24" aria-hidden="true"><circle cx="12" cy="12" r="11" fill="none" stroke="#fff" stroke-width="2"/><rect x="6" y="8" width="12" height="8" fill="none" stroke="#fff" stroke-width="1.6"/><path d="M6 8l6 5 6-5" fill="none" stroke="#fff" stroke-width="1.6"/></svg>
      info@vintrelcorp.com
    </span>
    <span class="contact-item">
      <svg viewBox="0 0 24 24" aria-hidden="true"><g fill="none" stroke="#fff" stroke-width="1.6"><circle cx="12" cy="12" r="10"/><ellipse cx="12" cy="12" rx="4.5" ry="10"/><path d="M2 12h20M4 7h16M4 17h16"/></g></svg>
      www.vintrelcorp.com
    </span>
  </footer>
</main>
</body>
</html>
```